Bold Harbor Web Design Layout (no HTML)

We require the layout only for a website.  No html or logo is required - just the layout.

A refreshed and revitalized website to coincide with the relaunch of our brand. We are looking for a clean simplistic design that is easy to use and presents relevant information effectively.
We are an events management company specializing in conferences.
Updates

Thank you for your design. We really like the imagery. Essentially we are after a home page design (one page) that incorporates the 3 main buttons (request a proposal, select a venue and specials) while providing the relevant information on our service via functionality similar to that on www.plivtrak.com ie using the large arrow to scroll over the relevant topic to receive information. We hope to finalise the contest in the next week and hope to consider your revised entry.

Thanks!

Target Market(s)

Australian corporate sector primarily Managing Directors or their assistants. Any business looking to hold a conference for up 500 delegates however we are primarily targeting the decision maker so need to ensure we are communicating on their terms.

Industry/Entity Type

Event

Requirements
Must have
• Incorporate the elements from the attached document however with complete creative license as to their layout. Our main competitors are gathorly.com.au, talkhollowhq.com.au both sites are bland and not user friendly.
Nice to have
• Colours red, silver and black. Note we are running a separate contest to refresh our logo.
• We like the functionality of plivtrak.com

```html
<!DOCTYPE html>
<html lang="en">
<head>
<meta charset="utf-8">
<title>Bold Harbor – Conference Management</title>
<link href="https://fonts.googleapis.com/css2?family=Didact+Gothic&family=Arimo:wght@400;700&display=swap" rel="stylesheet">
<style>
:root{
  --black:#000;
  --white:#fff;
  --red:#e8000b;
  --red-dark:#b30008;
  --panel-grey:#e6e6e6;
  --text-grey:#6b6b6b;
  --ink:#111;
  --silver-hi:#f4f4f4;
  --silver-mid:#9a9a9a;
  --silver-dark:#3a3a3a;
}
*{box-sizing:border-box;margin:0;padding:0}
html,body{width:1200px;height:685px;overflow:hidden;background:var(--black)}
body{position:relative;font-family:"Didact Gothic",sans-serif;color:var(--ink)}
.band{position:absolute;left:0;top:96px;width:1200px;height:40px;background:var(--white)}
.page{position:absolute;left:157px;top:7px;width:882px;height:622px;background:var(--white);border-radius:8px}
.header{position:absolute;left:8px;top:6px;width:866px;height:81px;border-radius:6px 6px 0 0;
  background:linear-gradient(180deg,#2a2a2a 0%,var(--silver-mid) 12%,var(--silver-hi) 24%,#8c8c8c 42%,#6d6d6d 55%,#b5b5b5 75%,var(--silver-dark) 100%)}
.logo-text{position:absolute;left:39px;top:49px;font:700 10px "Arimo",sans-serif;color:var(--white);letter-spacing:.2px}
.search{position:absolute;left:586px;top:44px;display:flex;align-items:center}
.search-label{font:700 15px "Arimo",sans-serif;color:var(--white);margin-right:2px}
.search-field{width:178px;height:21px;background:var(--white);border:1px solid #777}
.search-go{margin-left:2px;width:27px;height:27px;border-radius:3px;background:linear-gradient(#f22,#a00);border:1px solid #600;
  font:700 12px "Arimo",sans-serif;color:var(--white);display:flex;align-items:center;justify-content:center}
.nav{position:absolute;left:10px;top:89px;width:864px;height:40px;background:var(--black);display:flex;align-items:center;padding-left:69px;gap:11px}
.nav a{font:14px "Didact Gothic",sans-serif;color:var(--white);text-decoration:none}
.nav a.current{font-weight:700;color:#d8e4f0;position:relative}
.nav a.current::after{content:"";position:absolute;left:50%;bottom:-14px;margin-left:-6px;border:6px solid transparent;border-bottom-color:var(--white)}
.side-menu{position:absolute;left:9px;top:185px;width:135px}
.side-menu li{list-style:none;height:28px;line-height:28px;padding-left:19px;font-size:14.5px;color:#222}
.side-menu li.active{color:var(--white);background:var(--red);border-radius:3px 0 0 3px;
  clip-path:polygon(0 0,92% 0,100% 50%,92% 100%,0 100%);box-shadow:0 2px 4px #999}
.divider{position:absolute;top:160px;width:2px;height:430px;background:linear-gradient(#fff,#bbb 40%,#bbb 70%,#fff)}
.intro{position:absolute;left:171px;top:154px;width:480px;font-size:17px;line-height:19px;color:var(--ink)}
.intro b{font-weight:700;font-family:"Arimo",sans-serif}
.finance{position:absolute;left:156px;top:230px;width:495px;height:238px;background:var(--panel-grey);border-radius:8px}
.finance h2{position:absolute;left:33px;top:11px;font:700 14.5px "Arimo",sans-serif;color:var(--text-grey)}
.finance-art{position:absolute;left:30px;top:58px;width:115px;height:160px;border-radius:40% 40% 30% 30%;
  background:radial-gradient(circle at 55% 40%,#e3201b,#9c0f0a 70%,rgba(180,180,180,.35))}
.finance ul{position:absolute;left:160px;top:46px;font-size:14px;line-height:15.8px;color:var(--text-grey)}
.finance li{list-style:none;padding-left:15px;position:relative}
.finance li::before{content:"•";position:absolute;left:0}
.finance p{position:absolute;left:159px;top:173px;width:330px;font-size:14px;line-height:15.8px;color:var(--text-grey)}
.goals{position:absolute;left:659px;top:146px;width:203px;height:326px;border-radius:7px;
  background:linear-gradient(180deg,#ff1c1c 0%,var(--red) 30%,var(--red-dark) 100%)}
.goals h3{position:absolute;left:6px;top:34px;font:400 18px "Didact Gothic",sans-serif;line-height:21px;color:var(--white)}
.goals ul{position:absolute;left:12px;top:176px}
.goals li{list-style:none;font-size:20px;line-height:21px;color:var(--white);margin-bottom:17px}
.pointer{position:absolute;left:604px;top:253px}
.pointer span{position:absolute;left:70px;top:13px;font-size:20px;color:var(--white)}
.promo{position:absolute;top:484px;width:200px;height:100px}
.promo h4{height:18px;line-height:18px;padding-left:8px;font:400 12px "Arimo",sans-serif;color:var(--white);
  background:var(--red);border-radius:0 4px 4px 4px}
.promo p{position:absolute;left:5px;top:24px;width:115px;font:400 11px "Arimo",sans-serif;line-height:12.5px;color:var(--ink)}
.promo-art{position:absolute;right:6px;top:26px;width:68px;height:68px;border-radius:50%}
.art-offer{background:radial-gradient(circle,#e32222,#9e0c0c)}
.art-clock{background:radial-gradient(circle,#fafafa 55%,#c41a1a 60%,#8a8a8a)}
.art-map{border-radius:40% 45% 35% 50%;background:radial-gradient(circle at 40% 40%,#ff4a3a,#b50e08)}
.footer{position:absolute;left:9px;top:589px;width:865px;height:24px;background:var(--black);border-radius:0 0 5px 5px;
  font:400 10px "Arimo",sans-serif;color:var(--white);text-align:center;line-height:24px}
</style>
</head>
<body>
<div class="band"></div>
<div class="page">
  <header class="header">
    <div class="logo-text">LOGO GOES HERE</div>
    <form class="search">
      <span class="search-label">SEARCH:</span>
      <span class="search-field"></span>
      <span class="search-go">GO</span>
    </form>
  </header>
  <nav class="nav">
    <a class="current">HOME</a><a>SERVICES</a><a>VENUES</a><a>CLIENTS</a><a>REGISTER</a><a>CONTACT US</a>
  </nav>

  <ul class="side-menu">
    <li class="active">OTHER MENU</li><li>OTHER MENU</li><li>OTHER MENU</li>
    <li>OTHER MENU</li><li>OTHER MENU</li><li>OTHER MENU</li>
  </ul>
  <div class="divider" style="left:145px"></div>

  <p class="intro"><b>Bold Harbor</b>' professional conference team specialises in solutions. We work closely with a core group of clients to ensure desired outcomes, on time and in budget.</p>

  <section class="finance">
    <h2>We offer a complete range of finance&nbsp; packages including;</h2>
    <div class="finance-art" role="img" aria-label="Large red dollar sign illustration"></div>
    <ul>
      <li>total conference underwriting</li>
      <li>online delegate payment gateway</li>
      <li>substantially discounted rooming rates</li>
      <li>no upfront costs</li>
      <li>zero management fees</li>
      <li>free venue sourcing</li>
      <li>free delegate booking management</li>
    </ul>
    <p>Minimise your costs and free your cash flow to focus on your core business functions. We'll ensure maximum return from your conference budget.</p>
  </section>

  <section class="goals">
    <h3>Our goal is to make<br>sure your conference is:</h3>
    <ul>
      <li>Expertely Managed<br>&amp; Hassle Free</li>
      <li>Outcome Focussed</li>
      <li>Well Attended</li>
    </ul>
  </section>
  <div class="pointer">
    <svg width="270" height="64" viewBox="0 0 270 64">
      <defs><linearGradient id="pointerFill" x1="0" y1="0" x2="0" y2="1">
        <stop offset="0" stop-color="#5a5a5a"/><stop offset="1" stop-color="#1e1e1e"/></linearGradient></defs>
      <path d="M2 32 L30 3 H262 a6 6 0 0 1 6 6 V55 a6 6 0 0 1 -6 6 H30 Z" fill="#fff"/>
      <path d="M7 32 L32 7 H259 a4 4 0 0 1 4 4 V53 a4 4 0 0 1 -4 4 H32 Z" fill="url(#pointerFill)"/>
    </svg>
    <span>Cost Effective</span>
  </div>

  <section class="promo" style="left:156px">
    <h4>Special Offers</h4>
    <p>Not sure where to start? We have over 60 properties to choose from both domestically and international.</p>
    <div class="promo-art art-offer" role="img" aria-label="Red dollar badge illustration"></div>
  </section>
  <div class="divider" style="left:381px;top:480px;height:110px"></div>
  <section class="promo" style="left:406px">
    <h4>Request Proposal</h4>
    <p>Not sure where to start? We have over 60 properties to choose from both domestically and international.</p>
    <div class="promo-art art-clock" role="img" aria-label="Wall clock illustration"></div>
  </section>
  <div class="divider" style="left:646px;top:480px;height:110px"></div>
  <section class="promo" style="left:661px">
    <h4>Browse Conference</h4>
    <p>Not sure where to start? We have over 60 properties to choose from both domestically and international.</p>
    <div class="promo-art art-map" role="img" aria-label="Red map of Australia illustration"></div>
  </section>

  <footer class="footer">Ph: 1300 555 214. P.O. Box 4471, Harbourside NSW 2099. Bold Harbor. All Rights Reserved. 2009</footer>
</div>
</body>
</html>
```